Mara Penrith Copywriter Website

I am starting a new business as a freelance copywriter. Trying to set up the website for my business is proving to be too technical for me. I would like a simple, clean website using primarily black and white. I have attached the logo I would like used. I would like the menu icons to be Home, Services, Portfolio, Blog, Contact. I would like my mobile phone number (0412 583 906) and email address (mara.penrith.copywriter@fernmail.test) used in the header of the site. I need the site to be easily manageable and inter-changeable for me to be able to move things around and add images, etc with ease.

I would like the home page to be a static page with space for an image of myself somewhere (I haven't had this taken as yet), an area to put a bit about myself and my business, and also somewhere to include social media icons/links. Again, I would like the whole website and home page to be easily managed so that I can add/delete things with ease.

I would like the image of the typewriter used in the website somewhere also please.

Coding

Coded - Design and coding required

Number of Pages Required

5+ page

Font styles to use
Sans Serif
Script

Colors
fdf0f6

Requirements
Must have
• The logo provided
• Ability to change page contents easily
• Ability to add social media icons as needed
Nice to have
• Use of the typewriter image
Should not have
• Complicated pages that are not easily editable

```html
<!DOCTYPE html>
<html lang="en">
<head>
<meta charset="utf-8">
<title>Mara Penrith Copywriter</title>
<link href="https://fonts.googleapis.com/css2?family=Mulish:wght@400;600;700&family=Playball&display=swap" rel="stylesheet">
<style>
:root{
  --ink:#111111;
  --text:#333333;
  --muted:#666666;
  --line:#d9d9d9;
  --paper:#ffffff;
  --band:#f2f2f2;
  --blush:#fdf0f6;
  --blush-deep:#f7dde6;
  --script:"Playball", cursive;
  --sans:"Mulish", sans-serif;
}
*{box-sizing:border-box;margin:0;padding:0}
html,body{width:1200px;height:3564px;overflow:hidden}
body{position:relative;background:var(--paper);font-family:var(--sans);color:var(--text)}
.abs{position:absolute}
a{color:inherit;text-decoration:none}

/* top bar */
.topbar{left:78px;top:0;width:1044px;height:52px;border-bottom:1px solid var(--line);display:flex;align-items:center;justify-content:space-between}
.social{display:flex;gap:16px}
.social span{width:14px;height:14px;border-radius:50%;background:var(--ink);display:block}
.contact-line{display:flex;gap:44px;font-size:14px;color:var(--text)}
.contact-line span{display:flex;align-items:center;gap:12px}

/* nav */
.brand{left:78px;top:76px;display:flex;align-items:center;gap:12px;font-family:var(--sans);font-weight:600;font-size:22px;color:var(--ink)}
.brand i{width:16px;height:16px;background:var(--blush-deep);display:block}
.nav{left:648px;top:91px;display:flex;gap:0;font-size:15px;letter-spacing:.5px;color:var(--text)}
.nav a{margin-right:46px}
.nav a:last-child{margin-right:0}
.nav .current{color:var(--ink);font-weight:700}

/* hero */
.hero-bg{left:0;top:162px;width:1200px;height:532px;background:linear-gradient(100deg,#f7f7f7 0%,#eeeeee 45%,#e6e6e6 100%)}
.hero-object{left:582px;top:190px;width:610px;height:404px;border-radius:40px;background:radial-gradient(ellipse at 55% 55%,#fbfbfb 0%,#e9e9e9 55%,rgba(230,230,230,0) 75%)}
.hero-title{left:78px;top:288px;font-family:var(--script);font-size:64px;color:var(--ink);line-height:1}
.hero-text{left:78px;top:376px;width:440px;font-size:18px;line-height:29px;color:var(--ink)}
.btn{display:flex;align-items:center;justify-content:center;background:var(--ink);color:var(--paper);font-weight:700;font-size:16px;letter-spacing:.5px;border-radius:24px;height:46px}
.hero-know{left:78px;top:489px;width:186px}
.hero-contact{left:286px;top:489px;width:187px}

/* newsletter */
.section-title{left:0;width:1200px;text-align:center;font-family:var(--script);font-size:40px;color:var(--ink);line-height:1}
.news-title{top:760px}
.news-form{left:297px;top:841px;width:606px;height:48px;border-radius:24px;background:var(--paper);box-shadow:0 2px 10px rgba(0,0,0,.12);display:flex;align-items:center}
.news-form .field{padding-left:38px;font-size:15px;color:var(--muted);flex:1}
.news-form .btn{width:167px;height:48px;font-size:18px}

/* about */
.about-accent{left:202px;top:967px;width:290px;height:245px;background:var(--blush-deep)}
.about-photo{left:78px;top:988px;width:392px;height:416px;background:linear-gradient(160deg,#9a9a8e 0%,#c9bca7 45%,#e6ddd0 80%,#b8b1a5 100%)}
.about-title{left:580px;top:1018px;font-family:var(--script);font-size:40px;color:var(--ink);line-height:1}
.about-text{left:575px;top:1078px;width:530px;font-size:14.5px;line-height:26px;color:var(--muted)}
.about-btn{left:575px;top:1316px;width:186px}

/* services */
.services-band{left:0;top:1490px;width:1200px;height:489px;background:var(--band)}
.services-title{top:1544px}
.services-card{left:78px;top:1609px;width:1044px;height:292px;background:var(--paper);box-shadow:0 2px 10px rgba(0,0,0,.08);display:flex;padding:40px 0}
.service{flex:1;text-align:center;border-right:1px solid var(--line);padding-top:14px}
.service:last-child{border-right:none}
.service svg{display:block;margin:0 auto}
.service h3{font-weight:400;font-size:21px;color:var(--ink);margin-top:16px}
.service hr{width:38px;border:none;border-top:3px solid var(--ink);margin:14px auto 14px}
.service p{font-size:14px;line-height:24px;color:var(--text);width:200px;margin:0 auto}
.service .more{display:inline-block;margin-top:10px;font-size:13px;color:var(--text);text-decoration:underline;letter-spacing:.5px}

/* portfolio */
.portfolio-title{top:2033px}
.tile{border:none}
.project{font-size:17px;color:var(--text)}

/* blog */
.blog-band{left:0;top:2875px;width:1200px;height:618px;background:var(--band)}
.blog-title{top:2930px}
.blog-photo{left:78px;top:2999px;width:521px;height:385px;background:linear-gradient(135deg,#3e2c22 0%,#6b4a36 40%,#a08873 70%,#5b4638 100%)}
.blog-card{left:599px;top:2999px;width:522px;height:385px;background:var(--paper);padding:70px 64px 0 64px}
.blog-card h3{font-size:17px;line-height:29px;font-weight:700;color:var(--ink)}
.blog-card hr{width:38px;border:none;border-top:3px solid var(--ink);margin:16px 0 16px}
.blog-date{display:flex;align-items:center;gap:14px;font-size:14px;color:var(--ink)}
.blog-card p{margin-top:14px;font-size:14px;line-height:25px;color:var(--muted)}
.dots{left:560px;top:3418px;display:flex;gap:8px}
.dots span{width:16px;height:16px;border-radius:50%;border:2px solid var(--ink)}
.dots .active{background:var(--ink)}

/* footer */
.footer{left:0;top:3493px;width:1200px;height:71px;display:flex;align-items:center;justify-content:center;font-size:14px;color:var(--text)}
</style>
</head>
<body>

<header>
  <div class="abs topbar">
    <div class="social" aria-label="Social links">
      <span role="img" aria-label="Social profile link"></span>
      <span role="img" aria-label="Social profile link"></span>
      <span role="img" aria-label="Social profile link"></span>
      <span role="img" aria-label="Social profile link"></span>
    </div>
    <div class="contact-line">
      <span>
        <svg width="16" height="12" viewBox="0 0 16 12"><rect x="0.5" y="0.5" width="15" height="11" fill="#111"/><path d="M1 1l7 6 7-6" fill="none" stroke="#fff" stroke-width="1.3"/></svg>
        mara.penrith.copywriter@fernmail.test
      </span>
      <span>
        <svg width="16" height="16" viewBox="0 0 16 16"><path d="M3.5 1l3 3.2-1.8 1.8a10 10 0 0 0 5.3 5.3l1.8-1.8 3.2 3-2 2.3C7 14.6 1.4 9 .9 3z" fill="#111"/></svg>
        (0412 583 906)
      </span>
    </div>
  </div>

  <div class="abs brand"><i></i>mara penrith copywriter</div>
  <nav class="abs nav">
    <a class="current" href="#">HOME</a>
    <a href="#">SERVICES</a>
    <a href="#">PORTFOLIO</a>
    <a href="#">BLOG</a>
    <a href="#">CONTACT</a>
  </nav>
</header>

<section class="hero">
  <div class="abs hero-bg" role="img" aria-label="Soft background photo of a writing desk with papers"></div>
  <div class="abs hero-object" role="img" aria-label="Photo of a white vintage typewriter"></div>
  <h1 class="abs hero-title">mara penrith</h1>
  <p class="abs hero-text">Lorem Ipsum is simply dummy text of the printing and typesetting industry. Lorem Ipsum has been the industry's standard dummy text ever.</p>
  <a class="abs btn hero-know" href="#">KNOW MORE</a>
  <a class="abs btn hero-contact" href="#">CONTACT ME</a>
</section>

<section class="newsletter">
  <h2 class="abs section-title news-title">Subscribe to my Newsletter</h2>
  <div class="abs news-form">
    <span class="field">Enter your email</span>
    <span class="btn">SUBMIT</span>
  </div>
</section>

<section class="about">
  <div class="abs about-accent"></div>
  <div class="abs about-photo" role="img" aria-label="Portrait photo of the copywriter"></div>
  <h2 class="abs about-title">About mara penrith</h2>
  <p class="abs about-text">It was popularised in the 1960s with the release of Letraset sheets containing Lorem Ipsum passages, and more recently with desktop publishing software. An unknown printer took a galley of type and scrambled it to make a type specimen book. It has survived not only five centuries, but also the leap into electronic typesetting, remaining essentially unchanged.</p>
  <a class="abs btn about-btn" href="#">KNOW MORE</a>
</section>

<section class="services">
  <div class="abs services-band"></div>
  <h2 class="abs section-title services-title">Services</h2>
  <div class="abs services-card">
    <div class="service">
      <svg width="36" height="32" viewBox="0 0 36 32" fill="none" stroke="#111" stroke-width="1.6"><rect x="2" y="3" width="32" height="21"/><line x1="2" y1="8" x2="34" y2="8"/><line x1="13" y1="29" x2="23" y2="29"/><line x1="18" y1="24" x2="18" y2="29"/><rect x="11" y="12" width="14" height="8"/></svg>
      <h3>Landing Pages</h3><hr>
      <p>Lorem Ipsum is simply dummy text of the printing and typeset.</p>
      <a class="more" href="#">READ MORE</a>
    </div>
    <div class="service">
      <svg width="36" height="32" viewBox="0 0 36 32" fill="none" stroke="#111" stroke-width="1.6"><path d="M3 12v18h30V12"/><path d="M3 12l15 11 15-11"/><rect x="8" y="2" width="20" height="15"/><line x1="12" y1="7" x2="24" y2="7"/><line x1="12" y1="11" x2="24" y2="11"/></svg>
      <h3>Online sales letter</h3><hr>
      <p>Lorem Ipsum is simply dummy text of the printing and typeset.</p>
      <a class="more" href="#">READ MORE</a>
    </div>
    <div class="service">
      <svg width="36" height="32" viewBox="0 0 36 32" fill="none" stroke="#111" stroke-width="1.6"><rect x="8" y="1" width="20" height="30"/><line x1="12" y1="7" x2="24" y2="7"/><line x1="12" y1="12" x2="24" y2="12"/><line x1="12" y1="17" x2="24" y2="17"/><line x1="12" y1="22" x2="20" y2="22"/></svg>
      <h3>Promotional emails</h3><hr>
      <p>Lorem Ipsum is simply dummy text of the printing and typeset.</p>
      <a class="more" href="#">READ MORE</a>
    </div>
    <div class="service">
      <svg width="36" height="32" viewBox="0 0 36 32" fill="none" stroke="#111" stroke-width="1.6"><path d="M3 13v17h30V13"/><path d="M3 13l15 11 15-11"/><path d="M10 17V4h16v13"/><path d="M14 10l3 3 6-6"/></svg>
      <h3>Email marketing</h3><hr>
      <p>Lorem Ipsum is simply dummy text of the printing and typeset.</p>
      <a class="more" href="#">READ MORE</a>
    </div>
  </div>
</section>

<section class="portfolio">
  <h2 class="abs section-title portfolio-title">Work Portfolio</h2>

  <div class="abs tile" style="left:78px;top:2098px;width:333px;height:250px;background:linear-gradient(135deg,#5a4a3c,#b59a7c 55%,#e2d6c6)" role="img" aria-label="Project photo: woman working at a laptop in a cafe"></div>
  <span class="abs project" style="left:80px;top:2370px">Project Name</span>
  <div class="abs tile" style="left:78px;top:2414px;width:333px;height:342px;background:linear-gradient(160deg,#c9c2b3,#a9a38f 50%,#6f6a5d)" role="img" aria-label="Project photo: child playing outdoors"></div>
  <span class="abs project" style="left:80px;top:2776px">Project Name</span>

  <div class="abs tile" style="left:432px;top:2098px;width:333px;height:345px;background:linear-gradient(160deg,#8d8a85,#d9cdb6 50%,#5f5c58)" role="img" aria-label="Project photo: person holding a straw hat"></div>
  <span class="abs project" style="left:434px;top:2465px">Project Name</span>
  <div class="abs tile" style="left:432px;top:2507px;width:333px;height:249px;background:linear-gradient(135deg,#d8d4cf,#e8c8b5 50%,#a3a09c)" role="img" aria-label="Project photo: woman with a toothbrush"></div>
  <span class="abs project" style="left:434px;top:2776px">Project Name</span>

  <div class="abs tile" style="left:789px;top:2098px;width:332px;height:250px;background:linear-gradient(180deg,#a8cfe0,#d7e4e8 45%,#e6a2a8 80%,#d9c9b5)" role="img" aria-label="Project photo: beach scene with boats"></div>
  <span class="abs project" style="left:791px;top:2370px">Project Name</span>
  <div class="abs tile" style="left:789px;top:2414px;width:332px;height:342px;background:linear-gradient(170deg,#e4ddd3,#c6b6a2 55%,#8c8378)" role="img" aria-label="Project photo: traveller with a suitcase on a city street"></div>
  <span class="abs project" style="left:791px;top:2776px">Project Name</span>
</section>

<section class="blog">
  <div class="abs blog-band"></div>
  <h2 class="abs section-title blog-title">Latest Blog</h2>
  <div class="abs blog-photo" role="img" aria-label="Blog photo: hands typing on a laptop"></div>
  <article class="abs blog-card">
    <h3>Lorem Ipsum is simply dummy text of the printing and typesetting industry Lorem Ipsum is simply.</h3>
    <hr>
    <div class="blog-date">
      <svg width="16" height="16" viewBox="0 0 16 16" fill="none" stroke="#111" stroke-width="1.4"><rect x="1" y="3" width="14" height="12"/><line x1="1" y1="7" x2="15" y2="7"/><line x1="5" y1="1" x2="5" y2="4"/><line x1="11" y1="1" x2="11" y2="4"/></svg>
      24 JUL 2018
    </div>
    <p>Lorem Ipsum is simply dummy text of the printing and typesetting industry. Lorem Ipsum has been the industry's standard dummy text ever since the 1500s, when an unknown printer took a galley of type and scrambled it to make a type specimen book.</p>
  </article>
  <div class="abs dots"><span></span><span></span><span></span><span class="active"></span></div>
</section>

<footer class="abs footer">2018 ©mara penrith- All Rights Reserved.</footer>

</body>
</html>
```